Business Card: RW Office Partners - Your organised problem solver

Business Name: RW Office Partners
Website: www.rwofficepartners.com.au
Email: marisol@rwofficepartners.com.au
Mobile: 61 482 907 236
Facebook: @rwofficepartners
Instrgram: @rwofficepartners

Brading Colours:
HEX
#986474
#ddccd3
#7a8498
#c9d8e4
#000000
#ffffff

Tag Line: Your organised problem solver

Link to DRAFT website:
https://deskhelpcollective.wixsite.com/rw-office-partners

About Page from the website:
My name is Marisol Wrenfield, and I would love to assist you to become more productive in your day to day and achieve your business and personal goals.
My mission is to give you time, time to work on the important tasks of your business or to be able to spend more time with your family. I will take on the tasks you don’t have time for, don’t know well or simply don’t like to do.
I have an extensive background in Administration, Tender Coordination, Document Control, WHS and Quality Management working primarily in the Construction, Mining and Corporate World.
I am passionate about being organised, having order and making things in your life (and mine) easier! I love to watch something unfold and grow into something amazing! I am known for being the go-to problem solver, the organiser of all things, producing high standards of work even under pressure. I’m also a confident communicator, and I understand that you’re busy running your business.

Target Market(s)

Small to Medium Business who require assistance in their business by a virtual assistant.

Industry/Entity Type

Virtual Assistant

Contact Information for Business Card

Mobile: 61 482 907 236

Font styles to use
Sans Serif

Colors
ffffff

Requirements
Must have
• Branding Colours as outlined.
Contact Details as outlined.
Logo as provided.
Proper contact details - mobile, facebook, instragm, website.
Simple, Elegant, very clean looking.
Should not have
• Note cute with pictures.
Not too girly as still want to market to construction companies.

```html
<!DOCTYPE html>
<html lang="en">
<head>
<meta charset="utf-8">
<title>RW Office Partners – Business Card</title>
<link rel="stylesheet" href="https://fonts.googleapis.com/css2?family=Roboto:wght@400;500&display=swap">
<style>
  :root {
    --mauve: #986474;
    --mauve-deep: #855a69;
    --mauve-soft: #ddccd3;
    --slate: #7a8498;
    --ice: #c9d8e4;
    --ink: #2a2a2a;
    --paper: #ffffff;
    --backdrop: #6e6a6a;
  }
  * { box-sizing: border-box; margin: 0; padding: 0; }
  html, body {
    width: 1200px; height: 1200px; overflow: hidden;
    background: var(--backdrop);
    font-family: "Roboto", Arial, sans-serif;
  }
  .canvas { position: relative; width: 1200px; height: 1200px; }
  .card {
    position: absolute; width: 712px; height: 418px;
    border-radius: 28px; overflow: hidden;
  }
  .card--front { left: 238px; top: 118px; background: var(--mauve-deep); }
  .card--back { left: 230px; top: 644px; background: var(--paper); }

  .wordmark {
    position: absolute; display: flex; align-items: center; gap: 16px;
    font-weight: 500; letter-spacing: 0.04em; text-transform: uppercase; white-space: nowrap;
  }
  .wordmark__square { display: block; }
  .card--front .wordmark {
    left: 0; right: 0; top: 0; bottom: 0; justify-content: center;
    color: var(--paper); font-size: 42px;
  }
  .card--front .wordmark__square { width: 34px; height: 34px; background: var(--paper); }
  .card--back .wordmark {
    left: 30px; top: 190px; color: var(--mauve-deep); font-size: 26px; gap: 12px;
  }
  .card--back .wordmark__square { width: 22px; height: 22px; background: var(--mauve-deep); }

  .contact-block { position: absolute; left: 382px; top: 94px; color: var(--ink); }
  .contact-block__name { font-size: 25px; font-weight: 500; color: var(--mauve-deep); line-height: 30px; }
  .contact-block__role { font-size: 17px; line-height: 22px; color: #3a3a3a; }
  .contact-list { list-style: none; margin-top: 20px; }
  .contact-list li {
    display: flex; align-items: center; gap: 13px;
    font-size: 17px; line-height: 24px; color: #333; white-space: nowrap;
  }
  .contact-list svg { width: 15px; height: 15px; flex: none; }
  .social-square { width: 13px; height: 13px; margin: 0 1px; background: var(--mauve-deep); border-radius: 2px; flex: none; }

  .card__bands { position: absolute; left: 0; bottom: 0; }
  .tagline {
    position: absolute; left: 382px; bottom: 17px;
    color: var(--paper); font-size: 17px; line-height: 22px;
  }
</style>
</head>
<body>
<main class="canvas">
  <section class="card card--front" aria-label="Card front">
    <div class="wordmark"><span class="wordmark__square"></span>RW Office Partners</div>
  </section>

  <section class="card card--back" aria-label="Card back">
    <div class="wordmark"><span class="wordmark__square"></span>RW Office Partners</div>

    <div class="contact-block">
      <h1 class="contact-block__name">Marisol Wrenfield</h1>
      <p class="contact-block__role">Virtual Assistant</p>
      <ul class="contact-list">
        <li>
          <svg viewBox="0 0 16 16" aria-hidden="true"><path fill="#555" d="M2 6c0-2 2-3 6-3s6 1 6 3v1h-3V5.5H5V7H2zM4 8h8l2 5H2z"/></svg>
          61 482 907 236
        </li>
        <li>
          <svg viewBox="0 0 16 16" aria-hidden="true"><rect x="1.5" y="3.5" width="13" height="9" fill="none" stroke="#555" stroke-width="1.4"/><path d="M1.5 3.5 8 9l6.5-5.5" fill="none" stroke="#555" stroke-width="1.4"/></svg>
          marisol@rwofficepartners.com.au
        </li>
        <li>
          <svg viewBox="0 0 16 16" aria-hidden="true"><circle cx="8" cy="8" r="6.3" fill="none" stroke="#777" stroke-width="1.2"/><ellipse cx="8" cy="8" rx="2.8" ry="6.3" fill="none" stroke="#777" stroke-width="1.1"/><path d="M1.7 8h12.6" stroke="#777" stroke-width="1.1"/></svg>
          www.rwofficepartners.com.au
        </li>
        <li><span class="social-square"></span>@rwofficepartners</li>
        <li><span class="social-square"></span>@rwofficepartners</li>
      </ul>
    </div>

    <svg class="card__bands" width="712" height="56" viewBox="0 0 712 56" aria-hidden="true">
      <rect x="0" y="36" width="330" height="20" fill="var(--slate)"/>
      <path d="M338 2 Q342 0 350 0 H712 V56 H312 Z" fill="var(--mauve-deep)"/>
    </svg>
    <p class="tagline">Your organised problem solver</p>
  </section>
</main>
</body>
</html>
```